KBT Business Cards

We require business cards for our business. We would like a matte black back to the card, with our logo centred in the middle. The front side of the card is open to design.

Target Market(s)

Clients looking for legal services (professional)

Industry/Entity Type

Legal

Contact Information for Business Card

Doran Kelbrath
Partner
Mobile: 0461 738 524
Email: doran@kbtlaw.co
Website: www.kbtlaw.co
Level 3, 118 Wendmore Street
Sydney NSW 2000

Font styles to use
Other font styles liked:
• Avenir

Colors
f04a50
ffffff
1b1b1b

Requirements
Must have
• Black back with logo included in the centre of the card.
• Our font is Avenir.

```html
<!DOCTYPE html>
<html lang="en">
<head>
<meta charset="utf-8">
<title>KBT Legal – Business Cards</title>
<link rel="stylesheet" href="https://fonts.googleapis.com/css2?family=Nunito+Sans:wght@400;600;700&display=swap">
<style>
  :root {
    --page-bg: #ebebeb;
    --card-back: #1f1d1e;
    --card-front: #29272a;
    --brand-red: #9e2440;
    --text-light: #ffffff;
    --text-soft: #f2f2f2;
  }
  * { box-sizing: border-box; margin: 0; padding: 0; }
  html, body {
    width: 1200px; height: 800px; overflow: hidden;
    background: var(--page-bg);
    font-family: "Nunito Sans", "Avenir", sans-serif;
  }
  .canvas { position: relative; width: 1200px; height: 800px; }
  .card {
    position: absolute; left: 316px; width: 570px; height: 329px;
    border-radius: 24px; overflow: hidden;
  }
  .card--back { top: 50px; background: var(--card-back); }
  .card--front { top: 420px; background: var(--card-front); }

  /* Back: centred wordmark */
  .wordmark {
    position: absolute; display: flex; align-items: center; gap: 18px;
  }
  .card--back .wordmark {
    left: 50%; top: 50%; transform: translate(-50%, -50%);
  }
  .wordmark__square { background: var(--brand-red); flex: none; }
  .card--back .wordmark__square { width: 44px; height: 44px; }
  .wordmark__name {
    color: var(--text-light); font-weight: 700; text-transform: uppercase;
    line-height: 0.98; letter-spacing: 0.01em;
  }
  .card--back .wordmark__name { font-size: 33px; }

  /* Front */
  .card--front .wordmark { left: 32px; top: 52px; gap: 12px; }
  .card--front .wordmark__square { width: 22px; height: 22px; }
  .card--front .wordmark__name { font-size: 16px; line-height: 1.02; }

  .person { position: absolute; left: 33px; top: 157px; }
  .person__name { color: var(--brand-red); font-size: 22px; font-weight: 600; letter-spacing: 0.01em; }
  .person__role { color: var(--text-soft); font-size: 16px; margin-top: 3px; }

  .contact-list { position: absolute; left: 32px; top: 226px; list-style: none; }
  .contact-list__item {
    display: flex; align-items: center; gap: 9px; height: 21px;
    color: var(--text-soft); font-size: 14px;
  }
  .contact-list__icon { width: 11px; height: 11px; fill: var(--brand-red); flex: none; }

  .address {
    position: absolute; right: 24px; top: 253px;
    padding-right: 8px; border-right: 1.5px solid var(--brand-red);
    color: var(--text-soft); font-size: 14px; line-height: 17px; text-align: right;
    font-style: normal;
  }
</style>
</head>
<body>
<main class="canvas">
  <section class="card card--back" aria-label="Card back">
    <div class="wordmark">
      <span class="wordmark__square"></span>
      <p class="wordmark__name">Kelbrath<br>Brant Thorne<br>Legal</p>
    </div>
  </section>

  <section class="card card--front" aria-label="Card front">
    <div class="wordmark">
      <span class="wordmark__square"></span>
      <p class="wordmark__name">Kelbrath<br>Brant Thorne<br>Legal</p>
    </div>

    <div class="person">
      <h1 class="person__name">Doran Kelbrath</h1>
      <p class="person__role">Partner</p>
    </div>

    <ul class="contact-list">
      <li class="contact-list__item">
        <svg class="contact-list__icon" viewBox="0 0 24 24" aria-hidden="true"><path d="M6.6 10.8a15.1 15.1 0 0 0 6.6 6.6l2.2-2.2c.3-.3.7-.4 1-.2 1.1.4 2.3.6 3.6.6.6 0 1 .4 1 1V20c0 .6-.4 1-1 1C10.6 21 3 13.4 3 4c0-.6.4-1 1-1h3.5c.6 0 1 .4 1 1 0 1.3.2 2.5.6 3.6.1.3 0 .7-.2 1z"/></svg>
        <span>0461 738 524</span>
      </li>
      <li class="contact-list__item">
        <svg class="contact-list__icon" viewBox="0 0 24 24" aria-hidden="true"><path d="M2 5h20v14H2z M4 7v.5l8 5 8-5V7l-8 5z" fill-rule="evenodd"/></svg>
        <span>doran@kbtlaw.co</span>
      </li>
      <li class="contact-list__item">
        <svg class="contact-list__icon" viewBox="0 0 24 24" aria-hidden="true"><circle cx="12" cy="12" r="10"/></svg>
        <span>www.kbtlaw.co</span>
      </li>
    </ul>

    <address class="address">Level 3, 118 Wendmore<br>Street Sydney NSW 2000</address>
  </section>
</main>
</body>
</html>
```